Harbourline Electrical Solutions

On one side. LOGO (underneath:) Commercial Industrial Residential

- NAME & CONTACT DETAILS

Marcus T. Hollings
Project Manager

(Cell icon) (441) 555-0187
(Email icon) hlelectricalsolutions@mailvento.com
(Facebook & Instagram icons )@hlelectricalsolutions

Other side: LOGO - underneath ELECTRICAL CONSTRUCTION & MAINTENANCE . LED LIGHTING & AUTOMATION . LIFE SAFETY SYSTEMS (FIRE ALARM / SECURITY) . DATA & COMMUNICATION

```html
<!DOCTYPE html>
<html lang="en">
<head>
<meta charset="utf-8">
<title>Harbourline Electrical Solutions – Business Card</title>
<link rel="stylesheet" href="https://fonts.googleapis.com/css2?family=Montserrat:wght@400;500;600&display=swap">
<style>
  :root {
    --teal: #10566b;
    --grey: #5a5a5c;
    --ink: #2e2e30;
    --white: #ffffff;
    --backdrop: #e9e5de;
  }
  * { box-sizing: border-box; margin: 0; padding: 0; }
  html, body { width: 1200px; height: 900px; overflow: hidden; }
  body {
    background: var(--backdrop);
    font-family: "Montserrat", Arial, sans-serif;
    position: relative;
  }
  .card {
    position: absolute;
    left: 311px;
    width: 577px;
    height: 329px;
    overflow: hidden;
    box-shadow: 0 2px 6px rgba(0,0,0,0.18);
  }
  /* Front side */
  .card--front { top: 98px; background: var(--teal); color: var(--white); }
  .brand {
    display: flex;
    align-items: center;
    gap: 12px;
  }
  .brand__mark { width: 34px; height: 34px; }
  .brand__name {
    font-weight: 500;
    font-size: 14px;
    line-height: 15px;
    letter-spacing: 1.6px;
    text-transform: uppercase;
  }
  .card--front .brand {
    position: absolute;
    left: 0; right: 0; top: 135px;
    justify-content: center;
  }
  .card--front .brand__mark { background: var(--white); }
  .services {
    position: absolute;
    left: 0; right: 0; top: 262px;
    text-align: center;
    font-size: 13.5px;
    line-height: 16px;
    letter-spacing: 0.6px;
    font-weight: 500;
  }
  /* Back side */
  .card--back { top: 472px; background: var(--white); }
  .card--back .brand { position: absolute; left: 30px; top: 36px; color: var(--teal); }
  .card--back .brand__mark { background: var(--teal); width: 40px; height: 40px; }
  .sectors {
    position: absolute; left: 30px; top: 100px;
    color: var(--teal); font-size: 14px; font-weight: 500;
  }
  .contact {
    position: absolute; right: 34px; top: 144px;
    text-align: right;
  }
  .contact__role { font-size: 13px; color: var(--ink); line-height: 16px; }
  .contact__name { font-size: 18px; color: var(--teal); font-weight: 500; line-height: 22px; margin-bottom: 8px; }
  .contact__line {
    display: flex; justify-content: flex-end; align-items: center; gap: 6px;
    font-size: 14px; color: var(--ink); line-height: 23px;
  }
  .contact__icon { width: 18px; height: 18px; }
  .wave { position: absolute; left: 0; bottom: 0; width: 577px; height: 70px; }
  .social {
    position: absolute; left: 32px; bottom: 22px;
    display: flex; align-items: center; gap: 8px;
    color: var(--white); font-size: 14px;
  }
  .social__dot { width: 15px; height: 15px; border-radius: 50%; background: var(--white); }
</style>
</head>
<body>

<section class="card card--front">
  <div class="brand">
    <span class="brand__mark"></span>
    <span class="brand__name">Harbourline<br>Electrical<br>Solutions</span>
  </div>
  <p class="services">
    ELECTRICAL CONSTRUCTION &amp; MAINTENANCE<br>
    LIFE SAFETY SYSTEMS (FIRE ALARM | SECURITY)<br>
    LED LIGHTING &amp; AUTOMATION &nbsp;|&nbsp; DATA &amp; COMMUNICATION
  </p>
</section>

<section class="card card--back">
  <div class="brand">
    <span class="brand__mark"></span>
    <span class="brand__name">Harbourline<br>Electrical<br>Solutions</span>
  </div>
  <p class="sectors">Commercial Industrial Residential</p>

  <div class="contact">
    <p class="contact__role">Project Manager</p>
    <p class="contact__name">Marcus T. Hollings</p>
    <p class="contact__line">(441) 555-0187
      <svg class="contact__icon" viewBox="0 0 18 18" aria-hidden="true">
        <circle cx="9" cy="9" r="9" fill="var(--teal)"/>
        <rect x="6" y="3.5" width="6" height="11" rx="1.2" fill="none" stroke="#fff" stroke-width="1.3"/>
        <circle cx="9" cy="12.4" r="0.8" fill="#fff"/>
      </svg>
    </p>
    <p class="contact__line">hlelectricalsolutions@mailvento.com
      <svg class="contact__icon" viewBox="0 0 18 18" aria-hidden="true">
        <circle cx="9" cy="9" r="9" fill="var(--teal)"/>
        <rect x="4.5" y="5.8" width="9" height="6.4" fill="none" stroke="#fff" stroke-width="1.1"/>
        <path d="M4.8 6.2 L9 9.4 L13.2 6.2" fill="none" stroke="#fff" stroke-width="1.1"/>
      </svg>
    </p>
  </div>

  <svg class="wave" viewBox="0 0 577 70" preserveAspectRatio="none" aria-hidden="true">
    <path d="M330 30 C440 36 530 22 577 0 L577 18 C535 38 445 44 330 30 Z" fill="var(--grey)"/>
    <path d="M0 22 C120 0 260 8 380 36 C470 55 540 48 577 30 L577 70 L0 70 Z" fill="var(--teal)"/>
  </svg>
  <div class="social">
    <span class="social__dot"></span>
    <span>@hlelectricalsolutions</span>
  </div>
</section>

</body>
</html>
```